Interior designer needs a power point template design

I need a template PowerPoint design for my client presentations. The presentations I prepare for my clients usually include the furniture project, the detail of the selected furniture, and the costs. There are a lot of images I insert. What I need is to have a template that I can use for all my presentations, where from time to time I will insert the specific images and descriptions I want to insert. What will always be the same will be the cover, the colors, the font, and the design of the internal sections.
I already have my logo that I would like to insert on each page of the presentation (in small size).
In summary, I need:
- basic template design
- cover with an image chosen by Pictavale photo
- design an internal section/chapter
- internal page design.

I like the clolors of pink and brown <8please see image attached)
Images (will come from Pictavale photo)
● entrance/hall
● living room
● dining room
● Bathroom
● Closet
● Kids room
● Master bedroom
● Master bathroom
● Kitchen
● Office
● Laundry
● Balcony or Terrace

Target Market(s)

Customers (both residential and commercial projects)

Industry/Entity Type

interior design

Font styles to use
Other font styles liked:
• I like courier new

Requirements
Must have
• beautiful design
Should not have
• animations

```html
<!DOCTYPE html>
<html lang="it">
<head>
<meta charset="utf-8">
<title>Casa Lume — Template presentazione</title>
<link href="https://fonts.googleapis.com/css2?family=Questrial&family=Barlow:wght@400;500&family=Josefin+Sans:wght@200;300&display=swap" rel="stylesheet">
<style>
  :root{
    --page:#1e1e21;
    --slide:#f7f5f5;
    --frame:#f2b0b3;
    --pink:#ffb4b6;
    --brown:#7b5657;
    --ink:#2a2a2a;
    --cream:#f3eee6;
    --accent:#ee8f98;
    --wood-1:#c9b091;
    --wood-2:#b8997a;
    --bloom:#6e4a3c;
    --peach-1:#fde6cc;
    --peach-2:#f6c99b;
    --teal-1:#74c6cb;
    --teal-2:#2f7480;
  }
  *{box-sizing:border-box;margin:0;padding:0}
  html,body{width:1200px;height:4090px;overflow:hidden;background:var(--page)}
  body{position:relative;font-family:'Barlow',sans-serif;color:var(--ink)}

  .slide{position:absolute;left:29px;width:1142px;background:var(--slide);border:3px solid var(--frame);overflow:hidden}

  .slide--cover{top:24px;height:643px;border:none}
  .cover-art{position:absolute;inset:0;
    background:
      linear-gradient(90deg,rgba(0,0,0,0) 0%,rgba(0,0,0,0) 42%,rgba(110,74,60,.35) 55%,rgba(110,74,60,.15) 68%,rgba(150,70,60,.35) 82%,rgba(240,230,220,.35) 90%,rgba(110,74,60,.25) 100%),
      linear-gradient(180deg,var(--wood-1) 0%,var(--wood-2) 100%)}
  .cover-panel{position:absolute;left:19px;top:21px;width:414px;height:555px;background:var(--cream);
    display:flex;flex-direction:column;align-items:center;justify-content:flex-end;padding-bottom:120px}

  .brand-name{font-family:'Josefin Sans',sans-serif;font-weight:200;color:#3a3a3a;letter-spacing:6px;text-align:center;line-height:1;white-space:nowrap}
  .cover-panel .brand-name{font-size:76px}
  .brand-tag{font-family:'Josefin Sans',sans-serif;font-weight:200;color:#3a3a3a;letter-spacing:7px;font-size:17px;margin-top:16px;white-space:nowrap}

  .corner-logo{position:absolute;top:22px;width:80px;text-align:center}
  .corner-logo .brand-name{font-size:16px;letter-spacing:1px;line-height:1.05}
  .corner-logo .brand-tag{font-size:5px;letter-spacing:1.2px;margin-top:3px}
  .corner-logo--right{right:12px}
  .corner-logo--left{left:12px}

  .visual{position:absolute;top:44px;width:635px;height:555px;border-radius:12px;overflow:hidden}
  .visual--left{left:30px}
  .visual--right{left:483px}
  .visual--bedroom-art{background:
      linear-gradient(180deg,rgba(255,255,255,0) 0%,rgba(255,255,255,0) 50%,rgba(56,150,210,.55) 62%,rgba(56,150,210,.2) 72%,rgba(200,140,90,.35) 82%,rgba(255,255,255,0) 92%),
      linear-gradient(90deg,#7fb59a 0%,var(--peach-1) 14%,#e9eef2 22%,#e9eef2 38%,var(--peach-1) 48%,var(--peach-2) 100%)}
  .visual--bedroom-render{background:
      linear-gradient(180deg,#d7d9dc 0%,#c9ccd0 40%,#3b3f48 58%,#2c3038 70%,#9a6a40 80%,#7a5030 100%)}
  .visual--closet-art{background:
      linear-gradient(90deg,rgba(255,255,255,0) 0%,rgba(255,255,255,.75) 22%,rgba(255,255,255,.75) 78%,rgba(255,255,255,0) 100%),
      linear-gradient(180deg,var(--teal-1) 0%,#5cb8bf 60%,var(--teal-2) 100%)}
  .visual--closet-render{background:
      linear-gradient(180deg,#e4e4e7 0%,#2b2b33 8%,#4a4550 22%,#f1f1f3 30%,#f1f1f3 38%,#2e2c34 46%,#5a5460 66%,#eeeef0 82%,#ffffff 100%)}

  .textbox{position:absolute;top:93px;width:413px;height:436px;padding:38px 30px 0;text-align:center;
    box-shadow:0 4px 14px rgba(0,0,0,.12)}
  .textbox--pink{left:628px;background:var(--pink);color:var(--ink)}
  .textbox--brown{left:106px;background:var(--brown);color:#fff}
  .textbox h2{font-family:'Questrial',sans-serif;font-weight:400;font-size:30px;letter-spacing:.5px;white-space:nowrap}
  .textbox .rule{display:block;width:64px;height:4px;margin:12px auto 16px;background:currentColor}
  .textbox p{font-size:14.2px;line-height:23.8px;text-align:justify;text-align-last:center}

  .thanks-logo{position:absolute;left:120px;top:360px;width:360px;text-align:center}
  .thanks-logo .brand-name{font-size:80px}
  .thanks-logo .brand-tag{font-size:18px}
  .divider{position:absolute;left:545px;top:110px;width:2px;height:465px;background:#555}
  .thanks-title{position:absolute;left:605px;top:165px;font-family:'Josefin Sans',sans-serif;font-weight:300;font-size:58px;color:var(--brown);letter-spacing:2px}
  .thanks-text{position:absolute;left:608px;top:234px;width:480px;font-size:13.4px;line-height:23px;color:#444}
  .contacts{position:absolute;left:612px;top:340px;list-style:none}
  .contacts li{display:flex;align-items:center;height:42px;font-size:15px;color:#333}
  .contacts svg{width:18px;height:18px;margin-right:14px;fill:var(--accent)}
</style>
</head>
<body>

<section class="slide slide--cover">
  <div class="cover-art" role="img" aria-label="Illustrazione di copertina: rami fioriti e figura femminile su fondo di legno"></div>
  <div class="cover-panel">
    <div class="brand-name">CASA</div>
    <div class="brand-name">LUME</div>
    <div class="brand-tag">INTERIOR DESIGN</div>
  </div>
</section>

<section class="slide" style="top:702px;height:641px">
  <div class="corner-logo corner-logo--right"><div class="brand-name">CASA<br>LUME</div><div class="brand-tag">INTERIOR DESIGN</div></div>
  <div class="visual visual--left visual--bedroom-art" role="img" aria-label="Illustrazione di una camera da letto con letto, piante e finestra"></div>
  <div class="textbox textbox--pink">
    <h2>CAMERA PADRONALE</h2><span class="rule"></span>
    <p>Lorem ipsum dolor sit amet, consectetur adipiscing elit, sed do eiusmod tempor incididunt ut labore et dolore magna aliqua. Quis ipsum suspendisse ultrices gravida. Risus commodo viverra maecenas accumsan lacus vel facilisis. Sed ut perspiciatis unde omnis iste natus error sit voluptatem accusantium doloremque laudantium, totam rem aperiam, eaque ipsa quae ab illo inventore veritatis et quasi architecto beatae vitae dicta sunt explicabo. Nemo enim ipsam voluptatem quia voluptas sit aspernatur aut odit aut fugit, sed quia consequuntur magni dolores eos qui ratione voluptatem sequi nesciunt.</p>
  </div>
</section>

<section class="slide" style="top:1378px;height:641px">
  <div class="corner-logo corner-logo--left"><div class="brand-name">CASA<br>LUME</div><div class="brand-tag">INTERIOR DESIGN</div></div>
  <div class="visual visual--right visual--bedroom-render" role="img" aria-label="Render 3D della camera padronale con letto, lampadario e armadio"></div>
  <div class="textbox textbox--brown">
    <h2>CAMERA PADRONALE</h2><span class="rule"></span>
    <p>Lorem ipsum dolor sit amet, consectetur adipiscing elit, sed do eiusmod tempor incididunt ut labore et dolore magna aliqua. Quis ipsum suspendisse ultrices gravida. Risus commodo viverra maecenas accumsan lacus vel facilisis. Sed ut perspiciatis unde omnis iste natus error sit voluptatem accusantium doloremque laudantium, totam rem aperiam, eaque ipsa quae ab illo inventore veritatis et quasi architecto beatae vitae dicta sunt explicabo. Nemo enim ipsam voluptatem quia voluptas sit aspernatur aut odit aut fugit, sed quia consequuntur magni dolores eos qui ratione voluptatem sequi nesciunt.</p>
  </div>
</section>

<section class="slide" style="top:2055px;height:643px">
  <div class="corner-logo corner-logo--right"><div class="brand-name">CASA<br>LUME</div><div class="brand-tag">INTERIOR DESIGN</div></div>
  <div class="visual visual--left visual--closet-art" role="img" aria-label="Illustrazione di una cabina armadio con abiti colorati"></div>
  <div class="textbox textbox--pink">
    <h2>CABINA ARMADIO</h2><span class="rule"></span>
    <p>Lorem ipsum dolor sit amet, consectetur adipiscing elit, sed do eiusmod tempor incididunt ut labore et dolore magna aliqua. Quis ipsum suspendisse ultrices gravida. Risus commodo viverra maecenas accumsan lacus vel facilisis. Sed ut perspiciatis unde omnis iste natus error sit voluptatem accusantium doloremque laudantium, totam rem aperiam, eaque ipsa quae ab illo inventore veritatis et quasi architecto beatae vitae dicta sunt explicabo. Nemo enim ipsam voluptatem quia voluptas sit aspernatur aut odit aut fugit, sed quia consequuntur magni dolores eos qui ratione voluptatem sequi nesciunt.</p>
  </div>
</section>

<section class="slide" style="top:2733px;height:641px">
  <div class="corner-logo corner-logo--left"><div class="brand-name">CASA<br>LUME</div><div class="brand-tag">INTERIOR DESIGN</div></div>
  <div class="visual visual--right visual--closet-render" role="img" aria-label="Render 3D di una cabina armadio con abiti appesi e cassetti"></div>
  <div class="textbox textbox--brown">
    <h2>CABINA ARMADIO</h2><span class="rule"></span>
    <p>Lorem ipsum dolor sit amet, consectetur adipiscing elit, sed do eiusmod tempor incididunt ut labore et dolore magna aliqua. Quis ipsum suspendisse ultrices gravida. Risus commodo viverra maecenas accumsan lacus vel facilisis. Sed ut perspiciatis unde omnis iste natus error sit voluptatem accusantium doloremque laudantium, totam rem aperiam, eaque ipsa quae ab illo inventore veritatis et quasi architecto beatae vitae dicta sunt explicabo. Nemo enim ipsam voluptatem quia voluptas sit aspernatur aut odit aut fugit, sed quia consequuntur magni dolores eos qui ratione voluptatem sequi nesciunt.</p>
  </div>
</section>

<section class="slide slide--thanks" style="top:3409px;height:654px">
  <div class="thanks-logo"><div class="brand-name">CASA</div><div class="brand-name">LUME</div><div class="brand-tag">INTERIOR DESIGN</div></div>
  <div class="divider"></div>
  <h2 class="thanks-title">GRAZIE</h2>
  <p class="thanks-text">Sed ut perspiciatis unde omnis iste natus error sit voluptatem accusantium doloremque laudantium, totam rem aperiam, eaque ipsa quae ab illo inventore veritatis et quasi architecto beatae vitae dicta sunt explicabo.</p>
  <ul class="contacts">
    <li><svg viewBox="0 0 24 24"><path d="M6.6 10.8a15 15 0 0 0 6.6 6.6l2.2-2.2a1 1 0 0 1 1-.25 11.4 11.4 0 0 0 3.6.57 1 1 0 0 1 1 1V20a1 1 0 0 1-1 1A17 17 0 0 1 3 4a1 1 0 0 1 1-1h3.5a1 1 0 0 1 1 1c0 1.25.2 2.45.57 3.57a1 1 0 0 1-.25 1z"/></svg>347/5518042</li>
    <li><svg viewBox="0 0 24 24"><path d="M12 2a10 10 0 1 0 0 20 10 10 0 0 0 0-20zm6.9 6h-2.9a15.6 15.6 0 0 0-1.4-3.6A8 8 0 0 1 18.9 8zM12 4a14 14 0 0 1 1.9 4h-3.8A14 14 0 0 1 12 4zM4.3 14a8 8 0 0 1 0-4h3.4a16 16 0 0 0 0 4zm.8 2h2.9a15.6 15.6 0 0 0 1.4 3.6A8 8 0 0 1 5.1 16zM8 8H5.1a8 8 0 0 1 4.3-3.6A15.6 15.6 0 0 0 8 8zm4 12a14 14 0 0 1-1.9-4h3.8A14 14 0 0 1 12 20zm2.3-6H9.7a14.6 14.6 0 0 1 0-4h4.6a14.6 14.6 0 0 1 0 4zm.3 5.6A15.6 15.6 0 0 0 16 16h2.9a8 8 0 0 1-4.3 3.6zM16.3 14a16 16 0 0 0 0-4h3.4a8 8 0 0 1 0 4z"/></svg>www.casalume.com</li>
    <li><svg viewBox="0 0 24 24"><path d="M3 5h18a1 1 0 0 1 1 1v12a1 1 0 0 1-1 1H3a1 1 0 0 1-1-1V6a1 1 0 0 1 1-1zm9 7.5L20 7H4z"/></svg>studio@casalume.com</li>
    <li><svg viewBox="0 0 24 24"><path d="M12 2a7 7 0 0 0-7 7c0 5.2 7 13 7 13s7-7.8 7-13a7 7 0 0 0-7-7zm0 9.5A2.5 2.5 0 1 1 12 6.5a2.5 2.5 0 0 1 0 5z"/></svg>di Marta Velini via dei Tigli, 24</li>
  </ul>
</section>

</body>
</html>
```